Ecard for facebook and Instagram postings

I need 4 ecards (don't know if that is what it is called) for Facebook and Instagram postings. My Logo and company name should be incorporated and also be square. I would like to be able to insert text as I need. Examples are:

https://www.plorvexa.com/photo.php?fbid=20262841672382489&set=a.20261729249182489.516031.71298967488&type=1&relevant_count=1

https://media-a-kpt.yy.plorvexacdn.net/hpics-bmk4/2345967_657092986477056_308792573_n.jpg

I don't necessarily need images on them, just the color scheme to my business cards and the logo and business name. But if you'd like to give it an interesting look, you can go ahead and play with it. My site is tornquillmentoring.com, if you'd like to see the style of it.

Thank you!!!
Updates

I just uploaded the logo in two variations.  Thank you!

Target Market(s)

Women 16-65

Industry/Entity Type

Business

Requirements
Must have
• Logo and business name
Should not have
• No white background. I have attached business card picture so you can have an idea of what I'd like.

```html
<!DOCTYPE html>
<html lang="en">
<head>
<meta charset="utf-8">
<title>Tornquill Mentoring – Quote Card</title>
<link rel="stylesheet" href="https://fonts.googleapis.com/css2?family=Tinos:wght@700&family=Montserrat:wght@500&display=swap">
<style>
  :root {
    --band-top: #f39a22;
    --band-bottom: #c2262e;
    --quote-red: #c2262e;
    --ink: #0d0a08;
    --amber-light: #e6a86c;
    --amber-mid: #c98650;
    --amber-dark: #9c6036;
    --url-ink: #ffffff;
    --badge-fill: #f28a1c;
    --badge-ring: #ffffff;
  }
  html, body {
    margin: 0;
    padding: 0;
    width: 1200px;
    height: 1200px;
    overflow: hidden;
  }
  .card {
    position: relative;
    width: 1200px;
    height: 1200px;
    overflow: hidden;
    background: var(--amber-mid);
  }
  .card__backdrop {
    position: absolute;
    inset: 0;
    background:
      radial-gradient(circle at 18% 30%, rgba(255,210,160,0.55) 0, rgba(255,210,160,0) 22%),
      radial-gradient(circle at 80% 18%, rgba(255,200,150,0.45) 0, rgba(255,200,150,0) 20%),
      radial-gradient(circle at 25% 85%, rgba(255,215,170,0.6) 0, rgba(255,215,170,0) 28%),
      radial-gradient(circle at 85% 80%, rgba(255,190,130,0.5) 0, rgba(255,190,130,0) 26%),
      radial-gradient(ellipse at 50% 45%, var(--amber-light) 0, var(--amber-mid) 55%, var(--amber-dark) 100%);
  }
  .band {
    position: absolute;
    left: 0;
    width: 100%;
  }
  .band--top {
    top: 0;
    height: 20px;
    background: var(--band-top);
  }
  .band--bottom {
    bottom: 0;
    height: 25px;
    background: var(--band-bottom);
  }
  .quote-mark {
    position: absolute;
    font-family: "Tinos", "Times New Roman", serif;
    font-weight: 700;
    font-size: 330px;
    line-height: 1;
    color: var(--quote-red);
  }
  .quote-mark--open {
    left: 58px;
    top: 40px;
  }
  .quote-mark--close {
    left: 950px;
    top: 790px;
  }
  .quote {
    position: absolute;
    left: 150px;
    top: 220px;
    width: 900px;
    margin: 0;
    font-family: "Tinos", "Times New Roman", serif;
    font-weight: 700;
    font-size: 82px;
    line-height: 117px;
    text-align: center;
    color: var(--ink);
  }
  .brand {
    position: absolute;
    left: 32px;
    top: 1055px;
    font-family: "Tinos", "Times New Roman", serif;
    font-weight: 700;
    font-size: 50px;
    line-height: 1.1;
    color: var(--quote-red);
  }
  .brand__sub {
    display: block;
    font-size: 26px;
    letter-spacing: 8px;
  }
  .site-url {
    position: absolute;
    left: 548px;
    top: 1125px;
    font-family: "Montserrat", Arial, sans-serif;
    font-weight: 500;
    font-size: 29px;
    letter-spacing: 1px;
    color: var(--url-ink);
  }
  .badge {
    position: absolute;
    left: 1008px;
    top: 1035px;
    width: 130px;
    height: 130px;
  }
</style>
</head>
<body>
  <main class="card">
    <div class="card__backdrop" role="img" aria-label="Soft golden amber background with blurred light sparkles"></div>
    <div class="band band--top"></div>

    <span class="quote-mark quote-mark--open" aria-hidden="true">&ldquo;</span>
    <p class="quote">Ignorance is the curse of God; knowledge is the wing wherewith we fly to heaven</p>
    <span class="quote-mark quote-mark--close" aria-hidden="true">&rdquo;</span>

    <div class="brand">Tornquill Mentoring<span class="brand__sub">SERVICES</span></div>
    <div class="site-url">tornquillmentoring.com</div>

    <svg class="badge" viewBox="0 0 130 130" aria-hidden="true">
      <circle cx="65" cy="65" r="60" fill="var(--badge-fill)" stroke="var(--badge-ring)" stroke-width="7"/>
    </svg>

    <div class="band band--bottom"></div>
  </main>
</body>
</html>
```